Brell Stone Company Business Cards

Front and Back Business Card - logo and text setup - cool design. I need workable photoshop or illustrator files so I can setup each employee card with design that is created
Updates

Hi everyone, thank you for the great entries. Please no more white and blue cards - there are so many already - black and silver only now please. thanks!

Target Market(s)

Construction Industry - Facility Managers

Industry/Entity Type

Construction

Contact Information for Business Card

I really like contemporary simplistic looks - clean neat....not opposed to seeing some black backrounds

Requirements
Must have
• Logo/website address with design on front only - www.brellstone-example.com (logo attached)
• Back:
• Name/Title/Company Address/Phone/email address
Nice to have
• Cool design
Should not have
• Nothing gimmicky like Fire or Water - since we are a Fire Protection company - it has all been done

```html
<!DOCTYPE html>
<html lang="en">
<head>
<meta charset="utf-8">
<title>Brell Stone Company Business Cards</title>
<link rel="stylesheet" href="https://fonts.googleapis.com/css2?family=Lato:wght@400;700;900&display=swap">
<style>
  :root {
    --black: #151515;
    --silver: #b9bcc1;
    --silver-dark: #7d8187;
    --paper: #eceef0;
    --ink: #2b2b2b;
    --rule: #c4c7cb;
    --stage: #dcdcde;
    --white: #f5f6f7;
  }
  * { box-sizing: border-box; margin: 0; padding: 0; }
  html, body {
    width: 1200px; height: 782px; overflow: hidden;
    background: var(--stage);
    font-family: "Lato", Arial, sans-serif;
  }
  .canvas {
    position: relative; width: 1200px; height: 782px;
    display: flex; align-items: center; justify-content: center; gap: 60px;
  }
  .card {
    position: relative; width: 520px; height: 297px;
    box-shadow: 0 6px 18px rgba(0,0,0,0.22);
    overflow: hidden;
  }
  .card::after {
    content: ""; position: absolute; left: 0; right: 0; bottom: 0;
    height: 10px; background: var(--silver);
  }
  .card-front { background: var(--black); color: var(--white); }
  .card-back { background: var(--paper); }
  .card-back::after { background: var(--black); }

  .wordmark {
    font-weight: 900; font-size: 50px; letter-spacing: -1px; line-height: 1;
  }
  .card-front .wordmark {
    position: absolute; left: 0; right: 0; top: 100px; text-align: center;
    color: var(--silver);
  }
  .website {
    position: absolute; left: 0; right: 0; top: 218px; text-align: center;
    font-size: 15px; letter-spacing: 0.3px; color: var(--white);
  }

  .card-back .wordmark {
    position: absolute; left: 28px; top: 112px;
    font-size: 40px; color: var(--black);
  }
  .divider {
    position: absolute; left: 262px; top: 60px; width: 1px; height: 170px;
    background: var(--rule);
  }
  .contact {
    position: absolute; left: 282px; top: 76px; color: var(--ink);
  }
  .person-name {
    font-size: 19px; font-weight: 700; letter-spacing: 0.5px; color: var(--black);
    text-transform: uppercase;
  }
  .person-name .surname { color: var(--silver-dark); }
  .person-title { font-size: 15px; margin-bottom: 8px; }
  .contact-line {
    display: flex; align-items: center; gap: 7px;
    font-size: 15px; line-height: 1.45;
  }
  .contact-line svg { width: 13px; height: 13px; flex: none; fill: var(--black); }
  .address { font-size: 15px; line-height: 1.3; margin-top: 4px; }
</style>
</head>
<body>
<main class="canvas">
  <section class="card card-front" aria-label="Card front">
    <div class="wordmark">brellstone</div>
    <div class="website">www.brellstone-example.com</div>
  </section>

  <section class="card card-back" aria-label="Card back">
    <div class="wordmark">brellstone</div>
    <div class="divider"></div>
    <div class="contact">
      <div class="person-name">Daniel <span class="surname">Hart</span></div>
      <div class="person-title">Managing Director</div>
      <div class="contact-line">
        <svg viewBox="0 0 16 16" aria-hidden="true"><path d="M3 1h3l1.5 4-2 1.3a9 9 0 0 0 4.2 4.2L11 8.5l4 1.5v3a2 2 0 0 1-2 2A13 13 0 0 1 1 3a2 2 0 0 1 2-2z"/></svg>
        <span>044-987 654 321</span>
      </div>
      <div class="contact-line">
        <svg viewBox="0 0 16 16" aria-hidden="true"><path d="M1 3h14v10H1z M2 4.2v.5l6 4.3 6-4.3v-.5z" fill-rule="evenodd"/></svg>
        <span>info@brellstone-example.com</span>
      </div>
      <div class="address">421, Address line here,<br>45452, Country Name</div>
    </div>
  </section>
</main>
</body>
</html>
```